Simple and Clean business card design

We would like the design to be simple clean and to incorporate our colors.

We are open to your design and talent, we have the dots in our logo as we think of it as data points and we connect data points for people.

We are open to see the great creative and clean design you bring to the table

Contact Information for Business Card

please include: name, position, email, phone and website

Font styles to use
Sans Serif

Requirements
Must have
• my colors incorporated, simplicity
Nice to have
• lots of white space, simplicity
Should not have
• complexicity/ complex art

```html
<!DOCTYPE html>
<html lang="en">
<head>
<meta charset="utf-8">
<title>Nectaro Business Card</title>
<link rel="stylesheet" href="https://fonts.googleapis.com/css2?family=Montserrat:wght@400;500;600;700&display=swap">
<style>
  :root {
    --stage: #1f1f1f;
    --ink: #000000;
    --paper: #ffffff;
    --blue: #4285f4;
    --green: #34a853;
    --yellow: #fbbc05;
    --red: #ea4335;
  }
  * { box-sizing: border-box; margin: 0; padding: 0; }
  html, body {
    width: 1200px; height: 1015px; overflow: hidden;
    background: var(--stage);
    font-family: "Montserrat", sans-serif;
  }
  .stage { position: relative; width: 1200px; height: 1015px; }
  .card {
    position: absolute; left: 250px; width: 700px; height: 400px;
    overflow: hidden; box-shadow: 0 18px 40px rgba(0,0,0,.55);
  }
  .card--front { top: 60px; background: var(--ink); }
  .card--back { top: 530px; background: var(--paper); }

  .wordmark {
    position: absolute; display: flex; align-items: center; gap: 14px;
    font-weight: 600; letter-spacing: -1px; line-height: 1;
  }
  .wordmark__dot { width: 22px; height: 22px; border-radius: 50%; background: var(--blue); }
  .card--front .wordmark { left: 50%; top: 50%; transform: translate(-50%, -50%); color: var(--paper); font-size: 92px; }
  .card--back .wordmark { left: 50%; top: 62px; transform: translateX(-50%); color: var(--ink); font-size: 78px; }

  .person { position: absolute; left: 0; right: 0; top: 168px; text-align: center; }
  .person__name { font-size: 26px; font-weight: 700; color: var(--ink); }
  .person__role { font-size: 18px; font-weight: 500; color: var(--blue); margin-top: 2px; }

  .contact-band {
    position: absolute; left: 0; right: 0; bottom: 0; height: 96px; background: var(--ink);
  }
  .contact {
    position: absolute; top: -28px; width: 233px;
    display: flex; flex-direction: column; align-items: center;
  }
  .contact:nth-child(1) { left: 0; }
  .contact:nth-child(2) { left: 233px; }
  .contact:nth-child(3) { left: 466px; }
  .contact__icon {
    width: 56px; height: 56px; border-radius: 50%;
    border: 5px solid var(--paper);
    display: flex; align-items: center; justify-content: center;
  }
  .contact__icon--phone { background: var(--green); }
  .contact__icon--mail { background: var(--yellow); }
  .contact__icon--web { background: var(--red); }
  .contact__text { margin-top: 24px; font-size: 16px; color: var(--blue); letter-spacing: .3px; }
</style>
</head>
<body>
<main class="stage">
  <section class="card card--front" aria-label="Card front">
    <div class="wordmark"><span class="wordmark__dot"></span>nectaro</div>
  </section>

  <section class="card card--back" aria-label="Card back">
    <div class="wordmark"><span class="wordmark__dot"></span>nectaro</div>
    <div class="person">
      <p class="person__name">Marcus Lee</p>
      <p class="person__role">Founder/ CEO</p>
    </div>
    <div class="contact-band">
      <div class="contact">
        <span class="contact__icon contact__icon--phone">
          <svg width="26" height="26" viewBox="0 0 24 24" fill="#fff" aria-hidden="true"><path d="M6.6 10.8a15 15 0 0 0 6.6 6.6l2.2-2.2a1 1 0 0 1 1-.25 11.4 11.4 0 0 0 3.6.6 1 1 0 0 1 1 1V20a1 1 0 0 1-1 1A17 17 0 0 1 3 4a1 1 0 0 1 1-1h3.5a1 1 0 0 1 1 1c0 1.25.2 2.45.6 3.6a1 1 0 0 1-.25 1z"/></svg>
        </span>
        <span class="contact__text">555-014-2290</span>
      </div>
      <div class="contact">
        <span class="contact__icon contact__icon--mail">
          <svg width="28" height="20" viewBox="0 0 28 20" aria-hidden="true"><rect x="1" y="1" width="26" height="18" rx="2" fill="#fff"/><path d="M2 2l12 9 12-9" fill="none" stroke="#fbbc05" stroke-width="2"/></svg>
        </span>
        <span class="contact__text">marcus.lee@nectaro.one</span>
      </div>
      <div class="contact">
        <span class="contact__icon contact__icon--web">
          <svg width="28" height="28" viewBox="0 0 24 24" fill="none" stroke="#fff" stroke-width="1.6" aria-hidden="true"><circle cx="12" cy="12" r="9"/><ellipse cx="12" cy="12" rx="4" ry="9"/><path d="M3 12h18M5 7h14M5 17h14"/></svg>
        </span>
        <span class="contact__text">www.Nectaro.one</span>
      </div>
    </div>
  </section>
</main>
</body>
</html>
```